The design should look similar to the uploaded example to accommodate the information needed for a business card template. I would like to see the colors orange and charcoal grey incorporated along with the logo.The following should be on the back of the card SPECIALIZING IN NEW AND USED TIRES & WHEELS FOR:- Loaders- Skid Steers- Telehandlers- Boom Lifts- Forklifs and moreELIMINATING DOWNTIMEWheel Exchange Program for New & Used Foam Filled and Solid Rubber TiresSPECIALTY SERVICES- Foam Filling Tires- Largest Tire Press in SE- ONSITE Forklift Tire Press- Boom Truck Services - Rubber Tracks

Target Market(s)

New and Existing Customers

Industry/Entity Type

Business

Contact Information for Business Card

NAMEHEAVY DUTY TIRE, LLC8470 Belvedere RoadWest Palm Beach, FL 33411P: 844-HD-TIRESF: 561-431-6469C:E: W: WWW.GRANITERIMSUPPLY-EXAMPLE.COM

Font styles to use
Sans Serif

Colors
f37122
333333

Requirements
Must have
• The logo and the information indicated for the backside of the card
Nice to have
• Keep the orange and charcoal grey colors

```html
<!DOCTYPE html>
<html lang="en">
<head>
<meta charset="utf-8">
<title>Granite Rim Supply, LLC – Business Card</title>
<link href="https://fonts.googleapis.com/css2?family=Roboto:wght@400;500;700;900&display=swap" rel="stylesheet">
<style>
  :root {
    --orange: #f37122;
    --charcoal: #333333;
    --slate: #4a5560;
    --ink: #3a3a3a;
    --muted: #6b6b6b;
    --paper: #ffffff;
    --backdrop: #e9e7e3;
  }
  * { box-sizing: border-box; margin: 0; padding: 0; }
  html, body {
    width: 1200px; height: 950px; overflow: hidden;
    background: var(--backdrop);
    font-family: "Roboto", Arial, sans-serif;
    color: var(--ink);
  }
  .sheet { position: relative; width: 1200px; height: 950px; }
  .card {
    position: absolute; left: 250px; width: 700px; height: 400px;
    background: var(--paper);
    box-shadow: 0 6px 18px rgba(0,0,0,.18);
    overflow: hidden;
  }
  .card--back { top: 50px; }
  .card--front { top: 500px; }

  .brand { display: flex; align-items: center; gap: 14px; }
  .brand__dot {
    width: 46px; height: 46px; border-radius: 50%;
    background: var(--orange); flex: none;
  }
  .brand__name {
    font-weight: 900; color: var(--charcoal);
    font-size: 24px; line-height: 1.05; letter-spacing: .5px;
  }

  /* back */
  .card--back .brand { justify-content: center; margin-top: 42px; }
  .services { margin: 28px 50px 0; text-align: center; }
  .services__heading {
    font-weight: 700; font-size: 17px; color: var(--charcoal);
    letter-spacing: .3px; margin-top: 14px;
  }
  .services__heading:first-child { margin-top: 0; }
  .services__line { font-size: 15px; color: var(--muted); margin-top: 5px; }
  .services__line .sep { color: var(--orange); font-weight: 900; margin: 0 6px; }

  /* front */
  .card__band { position: absolute; inset: 0; }
  .card--front .brand { position: absolute; left: 40px; top: 58px; }
  .person { position: absolute; right: 40px; top: 88px; text-align: right; }
  .person__name { color: var(--orange); font-size: 22px; font-weight: 500; letter-spacing: .5px; }
  .person__title { color: #fff; font-size: 17px; letter-spacing: .5px; margin-top: 2px; }
  .contacts { position: absolute; left: 40px; top: 178px; list-style: none; }
  .contacts li { display: flex; align-items: center; gap: 10px; font-size: 17px; color: var(--ink); margin-bottom: 6px; }
  .contacts svg { width: 16px; height: 16px; fill: var(--charcoal); flex: none; }
  .address {
    position: absolute; right: 40px; bottom: 34px; text-align: right;
    font-size: 18px; line-height: 1.4; color: var(--muted); font-style: normal;
  }
</style>
</head>
<body>
<main class="sheet">

  <section class="card card--back" aria-label="Card back">
    <div class="brand">
      <span class="brand__dot"></span>
      <span class="brand__name">GRANITE RIM<br>SUPPLY, LLC</span>
    </div>
    <div class="services">
      <p class="services__heading">SPECIALIZING IN NEW AND USED TIRES &amp; WHEELS FOR</p>
      <p class="services__line">Loaders<span class="sep">•</span>Skid Steers<span class="sep">•</span>Telehandlers<span class="sep">•</span>Boom Lifts<span class="sep">•</span>Forklifs and more</p>
      <p class="services__heading">ELIMINATING DOWNTIME</p>
      <p class="services__line">Wheel Exchange Program for New &amp; Used Foam Filled and Solid Rubber Tires</p>
      <p class="services__heading">SPECIALTY SERVICES</p>
      <p class="services__line">Foam Filling Tires<span class="sep">•</span>Largest Tire Press in SE<span class="sep">•</span>ONSITE Forklift Tire Press</p>
      <p class="services__line">Boom Truck Services<span class="sep">•</span>Rubber Tracks</p>
    </div>
  </section>

  <section class="card card--front" aria-label="Card front">
    <svg class="card__band" viewBox="0 0 700 400" width="700" height="400" aria-hidden="true">
      <defs>
        <linearGradient id="bandShade" x1="0" y1="0" x2="1" y2="1">
          <stop offset="0" stop-color="#5a6570"/>
          <stop offset="1" stop-color="#3c4650"/>
        </linearGradient>
      </defs>
      <path d="M190 0 H700 V300 C560 250 400 140 190 0 Z" fill="var(--orange)"/>
      <path d="M200 0 H700 V282 C565 236 410 128 200 0 Z" fill="url(#bandShade)"/>
    </svg>

    <div class="brand">
      <span class="brand__dot"></span>
      <span class="brand__name">GRANITE RIM<br>SUPPLY, LLC</span>
    </div>

    <div class="person">
      <p class="person__name">MARCUS HALE</p>
      <p class="person__title">PRESIDENT</p>
    </div>

    <ul class="contacts">
      <li><svg viewBox="0 0 16 16"><path d="M3 1h3l1 4-2 1a9 9 0 0 0 5 5l1-2 4 1v3a2 2 0 0 1-2 2A13 13 0 0 1 1 3a2 2 0 0 1 2-2z"/></svg>844-GR-WHEEL</li>
      <li><svg viewBox="0 0 16 16"><path d="M4 0h8a1 1 0 0 1 1 1v14a1 1 0 0 1-1 1H4a1 1 0 0 1-1-1V1a1 1 0 0 1 1-1zm1 2v10h6V2zm3 11a1 1 0 1 0 0 2 1 1 0 0 0 0-2z"/></svg>555 512 7740</li>
      <li><svg viewBox="0 0 16 16"><path d="M4 0h7l1 1v4H4zM1 6h14v7H12v3H4v-3H1zm4 5v4h6v-4z"/></svg>561-278-9053</li>
      <li><svg viewBox="0 0 16 16"><path d="M0 3h16v1L8 9 0 4zm0 2.5 8 5 8-5V13H0z"/></svg>sales@graniterimsupply-example.com</li>
    </ul>

    <address class="address">
      5126 Marston Lane<br>
      Cedar Point, FL 34987<br>
      www.graniterimsupply-example.com
    </address>
  </section>

</main>
</body>
</html>
```